Flat Belly Design Graphics for Social

I want to create 9 social media graphics (new Instagram size 4:5 (1080 x 1350 pixels) focusing on our Flat Belly Graphics, using the pics attached. Use the attached pics, NO RANDOM STOCK PHOTOGRAPHY. For the color scheme of the graphics, the color palette is attached. YOU MUST POST ALL 9 GRAPHICS IN ONE ENTRY.
Using the 3 titles below, create one set of graphics. 1) with all text, then for the others, use the pictures as detailed below in IMPORTANT:
1. Ten-Week Bright Morning Reboot
2. The Quick Garden Kitchen Menu Guide
3. Studio Habits for Lasting Energy Past Midlife - Zero Gym Needed
IMPORTANT:
Only use RK Pic 1 and RK Pic 2 with the title, Ten-Week Bright Morning Reboot
Only use meal plan1 and meal plan2 pics with the title, Quick Garden Kitchen Menu Guide
Only use studio habits 1 and studio habits 2 pics with the title, Studio Habits for Lasting Energy Past Midlife - Zero Gym Needed
women over 40

```html
<!DOCTYPE html>
<html lang="en">
<head>
<meta charset="utf-8">
<title>Ten-Week Bright Morning Reboot – Social Set</title>
<link href="https://fonts.googleapis.com/css2?family=Bebas+Neue&family=Oswald:wght@500;600;700&family=Lato:wght@400;700;900&family=Damion&display=swap" rel="stylesheet">
<style>
  :root {
    --board: #4b4b4b;
    --pink: #e195ad;
    --blush: #fdeaef;
    --forest: #2c4a45;
    --white: #ffffff;
    --photo-warm: #d9b7a6;
    --photo-dark: #3a3330;
    --food-a: #e9c7a8;
    --food-b: #c96b5c;
    --food-c: #8fae6a;
  }
  * { margin: 0; padding: 0; box-sizing: border-box; }
  html, body { width: 1200px; height: 904px; overflow: hidden; }
  body { background: var(--board); position: relative; font-family: "Lato", sans-serif; }

  .post { position: absolute; overflow: hidden; }
  .post--hero { left: 35px; top: 30px; width: 442px; height: 556px; background: var(--blush); }
  .tile { width: 218px; height: 272px; }
  .col-1 { left: 490px; } .col-2 { left: 722px; } .col-3 { left: 953px; }
  .row-1 { top: 28px; } .row-2 { top: 314px; } .row-3 { top: 598px; }

  .abs { position: absolute; }
  .photo-person { background: linear-gradient(180deg, var(--photo-warm) 0%, #efe3dc 45%, var(--photo-dark) 100%); }
  .photo-friends { background: linear-gradient(160deg, #f2ebe6 0%, #c9a08a 55%, #e8dcd4 100%); }
  .photo-food { background: linear-gradient(135deg, var(--food-a) 0%, var(--food-b) 50%, var(--food-c) 100%); }

  .condensed { font-family: "Bebas Neue", "Oswald", sans-serif; line-height: .86; white-space: nowrap; }
  .oswald { font-family: "Oswald", sans-serif; font-weight: 700; line-height: .9; }
  .script { font-family: "Damion", cursive; line-height: 1; }
  .sans { font-family: "Lato", sans-serif; font-weight: 900; line-height: 1; }
  .center { text-align: center; }

  .c-pink { color: var(--pink); } .c-forest { color: var(--forest); } .c-white { color: var(--white); }

  .badge { position: absolute; border-radius: 50%; background: var(--white); display: flex; align-items: center; justify-content: center; text-align: center; color: var(--pink); }

  /* hero */
  .hero__vertical { left: 18px; top: 22px; }
  .hero__title { left: 215px; top: 52px; font-size: 38px; }
  .hero__sub { left: 216px; top: 90px; font-size: 30px; font-weight: 700; }
  .hero__photo { left: 200px; top: 136px; width: 242px; height: 420px; border-radius: 110px 110px 0 0; }
</style>
</head>
<body>

<!-- Hero post -->
<section class="post post--hero">
  <svg class="abs hero__vertical" width="184" height="522" viewBox="0 0 184 522" aria-label="Ten-Week">
    <text transform="translate(180 520) rotate(-90)" x="0" y="0" textLength="516" lengthAdjust="spacingAndGlyphs" font-family="'Bebas Neue', sans-serif" font-size="250" fill="var(--pink)">TEN-WEEK</text>
  </svg>
  <div class="abs hero__photo photo-person" role="img" aria-label="Smiling woman in a cropped white sweater pointing at her waist"></div>
  <div class="abs condensed c-forest hero__title">BRIGHT MORNING</div>
  <div class="abs sans c-pink hero__sub">REBOOT</div>
</section>

<!-- Menu guide, food border -->
<section class="post tile col-1 row-1" style="background:var(--pink)">
  <div class="abs photo-food" style="left:0;top:0;width:218px;height:46px" role="img" aria-label="Chicken breast, berries and bowls of grains along the top"></div>
  <div class="abs photo-food" style="left:0;top:46px;width:20px;height:170px" role="img" aria-label="Asparagus and chickpeas at the left edge"></div>
  <div class="abs photo-food" style="left:200px;top:46px;width:18px;height:120px" role="img" aria-label="Bowls of rice and nuts at the right edge"></div>
  <div class="abs condensed c-white" style="left:40px;top:62px;font-size:76px">QUICK</div>
  <div class="abs sans c-forest" style="left:42px;top:136px;font-size:14px">THE</div>
  <div class="abs condensed c-white" style="left:40px;top:154px;font-size:48px">GARDEN</div>
  <div class="abs sans c-forest" style="left:42px;top:204px;font-size:21px;font-weight:700;line-height:1.05">KITCHEN<br>MENU GUIDE</div>
</section>

<!-- Studio habits, pink top curve -->
<section class="post tile col-2 row-1" style="background:var(--white)">
  <div class="abs photo-friends" style="left:0;top:120px;width:218px;height:152px" role="img" aria-label="Two women sharing a secret, one looking surprised"></div>
  <svg class="abs" style="left:0;top:0" width="218" height="145" viewBox="0 0 218 145" aria-hidden="true"><path d="M0 0H218V128C160 118 80 122 0 145Z" fill="var(--pink)"/></svg>
  <div class="abs condensed c-white center" style="left:30px;top:12px;font-size:40px;width:150px">STUDIO<br>HABITS</div>
  <div class="abs sans c-white" style="left:172px;top:66px;font-size:8px;transform:rotate(-90deg);transform-origin:0 0">FOR</div>
  <div class="abs" style="left:30px;top:90px;width:160px;height:1px;background:var(--white)"></div>
  <div class="abs condensed c-forest" style="left:20px;top:96px;font-size:20px">LASTING ENERGY <span class="script c-white" style="font-size:17px">Past Midlife</span></div>
  <div class="abs sans c-white center" style="left:0;width:218px;top:124px;font-size:9px;font-weight:400">ZERO GYM NEEDED</div>
</section>

<!-- Reboot, pink column -->
<section class="post tile col-3 row-1" style="background:var(--blush)">
  <div class="abs" style="left:103px;top:0;width:115px;height:272px;background:var(--pink)"></div>
  <div class="abs photo-person" style="left:0;top:36px;width:160px;height:236px;border-radius:70px 70px 0 0" role="img" aria-label="Smiling woman in a white crop sweater pointing at her waist"></div>
  <div class="abs condensed c-white" style="left:113px;top:20px;font-size:54px">TEN</div>
  <div class="abs condensed c-white" style="left:214px;top:20px;font-size:24px;transform:rotate(90deg);transform-origin:0 0">WEEK</div>
  <div class="abs condensed c-forest" style="left:112px;top:80px;font-size:32px;text-align:right;width:98px">BRIGHT<br>MORNING</div>
  <div class="badge script" style="left:140px;top:192px;width:66px;height:66px;font-size:20px">Reboot</div>
</section>

<!-- Studio habits, blush with curve -->
<section class="post tile col-1 row-2" style="background:var(--blush)">
  <svg class="abs" style="left:0;top:0" width="218" height="272" viewBox="0 0 218 272" aria-hidden="true"><path d="M200 0H218V272H0V210C40 170 120 180 170 120C205 80 200 30 200 0Z" fill="var(--pink)"/></svg>
  <div class="abs photo-friends" style="left:88px;top:68px;width:130px;height:204px" role="img" aria-label="Two women whispering, one with a surprised expression"></div>
  <div class="abs sans c-pink" style="left:14px;top:12px;font-size:30px;line-height:.98">STUDIO<br>HABITS</div>
  <div class="abs sans c-forest" style="left:14px;top:80px;font-size:12px;font-weight:400">FOR</div>
  <div class="abs condensed c-forest" style="left:14px;top:94px;font-size:30px">LASTING<br>ENERGY</div>
  <div class="badge script" style="left:14px;top:160px;width:64px;height:64px;font-size:18px;line-height:.95">Past<br>Midlife</div>
  <div class="abs sans c-white center" style="left:10px;top:238px;width:90px;font-size:9px;font-weight:400">ZERO GYM NEEDED</div>
</section>

<!-- Reboot, forest -->
<section class="post tile col-2 row-2" style="background:var(--forest)">
  <div class="abs photo-person" style="left:100px;top:0;width:118px;height:272px;opacity:.9" role="img" aria-label="Smiling woman in a white crop sweater"></div>
  <div class="abs condensed c-pink" style="left:14px;top:32px;font-size:92px">TEN</div>
  <div class="abs condensed c-pink" style="left:122px;top:96px;font-size:16px">WEEK</div>
  <div class="abs condensed c-white" style="left:16px;top:120px;font-size:50px">BRIGHT</div>
  <div class="abs condensed c-white" style="left:16px;top:166px;font-size:28px">MORNING</div>
  <div class="abs script c-white center" style="left:14px;top:210px;width:88px;height:27px;border-radius:14px;background:var(--pink);font-size:19px;line-height:27px">Reboot</div>
</section>

<!-- Menu guide, notebook card -->
<section class="post tile col-3 row-2" style="background:var(--blush)">
  <div class="abs photo-food" style="inset:0" role="img" aria-label="Fresh vegetables, salmon, avocado and legumes surrounding a notebook"></div>
  <div class="abs" style="left:30px;top:42px;width:168px;height:212px;background:var(--white);border-radius:6px;transform:rotate(-5deg)"></div>
  <div class="badge" style="left:82px;top:60px;width:76px;height:76px;background:var(--pink)"><span class="condensed c-white" style="font-size:30px">QUICK</span></div>
  <div class="abs sans c-forest" style="left:54px;top:126px;font-size:14px">THE</div>
  <div class="abs condensed c-forest" style="left:58px;top:140px;font-size:40px;transform:rotate(-5deg)">GARDEN</div>
  <div class="abs sans c-pink" style="left:62px;top:178px;font-size:15px;transform:rotate(-5deg)">KITCHEN</div>
  <div class="abs oswald c-forest" style="left:66px;top:200px;font-size:20px;font-weight:500;transform:rotate(-5deg)">MENU GUIDE</div>
</section>

<!-- Reboot, pink -->
<section class="post tile col-1 row-3" style="background:var(--pink)">
  <div class="abs photo-person" style="left:104px;top:4px;width:114px;height:268px;border-radius:50px 0 0 0" role="img" aria-label="Woman in a sheer black top smiling downward"></div>
  <div class="abs condensed c-forest" style="left:8px;top:20px;font-size:76px">TEN</div>
  <div class="abs condensed c-forest" style="left:126px;top:18px;font-size:38px;transform:rotate(90deg);transform-origin:0 0">WEEK</div>
  <div class="abs condensed c-white" style="left:12px;top:100px;font-size:40px">BRIGHT</div>
  <div class="abs condensed c-white" style="left:12px;top:138px;font-size:28px">MORNING</div>
  <div class="badge script" style="left:15px;top:210px;width:52px;height:52px;font-size:15px">Reboot</div>
</section>

<!-- Menu guide, framed -->
<section class="post tile col-2 row-3" style="background:var(--pink)">
  <div class="abs photo-food" style="left:0;top:0;width:218px;height:28px" role="img" aria-label="Chicken and berries along the top"></div>
  <div class="abs photo-food" style="left:0;top:28px;width:22px;height:200px" role="img" aria-label="Asparagus and a menu card on the left"></div>
  <div class="abs photo-food" style="left:198px;top:28px;width:20px;height:200px" role="img" aria-label="Bowls of chickpeas and grains on the right"></div>
  <div class="abs photo-food" style="left:0;top:226px;width:218px;height:46px" role="img" aria-label="Fruit bowl and chicken breast along the bottom"></div>
  <div class="abs" style="left:42px;top:32px;width:134px;height:186px;border:1px solid var(--white);border-top:none"></div>
  <div class="abs condensed c-forest center" style="left:0;width:218px;top:24px;font-size:20px"><span style="background:var(--pink);padding:0 4px">THE</span></div>
  <div class="abs condensed c-white center" style="left:42px;width:134px;top:48px;font-size:64px">QUICK</div>
  <div class="abs condensed c-white center" style="left:42px;width:134px;top:108px;font-size:50px">GARDEN</div>
  <div class="abs sans c-forest center" style="left:0;width:218px;top:170px;font-size:18px;font-weight:700;line-height:1.05">KITCHEN<br>MENU GUIDE</div>
</section>

<!-- Studio habits, circle photo -->
<section class="post tile col-3 row-3" style="background:var(--blush)">
  <div class="abs photo-friends" style="left:-20px;top:-110px;width:258px;height:258px;border-radius:50%" role="img" aria-label="Two women whispering, one looking surprised"></div>
  <div class="abs condensed c-forest center" style="left:0;width:218px;top:162px;font-size:27px">STUDIO HABITS</div>
  <div class="abs sans c-forest center" style="left:0;width:218px;top:186px;font-size:10px;font-weight:400">FOR</div>
  <div class="abs condensed c-pink center" style="left:0;width:218px;top:198px;font-size:30px">LASTING ENERGY</div>
  <div class="abs script c-forest center" style="left:0;width:218px;top:224px;font-size:20px">Past Midlife</div>
  <div class="abs sans c-forest center" style="left:0;width:218px;top:255px;font-size:8px;font-weight:400">ZERO GYM NEEDED</div>
</section>

</body>
</html>
```